Parcelwise HQ letterhead and envelope

Design a formal (8.5x11) letterhead and envelope for sales outreach and legal matters. Using design input from https://www.parcelwisehq.example/ and the attached documents.

Industry/Entity Type

Software Service

Requirements
Must have
• These 4 hex colors are our official colors:
• #355c98 [blue]
• #1eb1a2 [teal]
• #fdba12 [gold]
• #f1653b [orange]
• So no other colors besides these should be used.

```html
<!DOCTYPE html>
<html lang="en">
<head>
<meta charset="utf-8">
<title>Parcelwise HQ Letterhead</title>
<link rel="stylesheet" href="https://fonts.googleapis.com/css2?family=Open+Sans:wght@400;600&family=Arimo:wght@700&family=Comfortaa:wght@400&display=swap">
<style>
  :root {
    --blue: #355c98;
    --teal: #1eb1a2;
    --gold: #fdba12;
    --orange: #f1653b;
    --ink: #2a2a2a;
    --paper: #fdfdfd;
    --backdrop: #e4e5e6;
  }
  * { box-sizing: border-box; margin: 0; padding: 0; }
  html, body { width: 1200px; height: 945px; overflow: hidden; }
  body { background: var(--backdrop); font-family: "Open Sans", sans-serif; color: var(--ink); }
  .sheet {
    position: absolute; left: 270px; top: 45px;
    width: 660px; height: 854px;
    background: var(--paper);
    box-shadow: 0 6px 18px rgba(0,0,0,0.12);
    overflow: hidden;
  }
  .sheet__header-bar { position: absolute; left: 0; top: 0; width: 100%; height: 14px; background: var(--blue); }
  .sheet__header-rule { position: absolute; left: 0; top: 18px; width: 100%; height: 4px; background: var(--teal); }
  .brand {
    position: absolute; left: 56px; top: 58px;
    display: flex; align-items: center; gap: 8px;
  }
  .brand__dot { width: 20px; height: 20px; border-radius: 50%; border: 2px solid var(--blue); }
  .brand__name { font-family: "Comfortaa", sans-serif; font-size: 22px; color: var(--blue); letter-spacing: 0.5px; }
  .letter { position: absolute; left: 84px; top: 222px; width: 492px; }
  .letter__salutation { font-family: "Arimo", sans-serif; font-weight: 700; font-size: 12.5px; margin-bottom: 10px; }
  .letter__para { font-size: 11px; line-height: 1.38; margin-bottom: 14px; text-align: justify; }
  .letter__signature {
    width: 120px; height: 44px; margin-top: 26px; margin-left: 70px;
    background: linear-gradient(90deg, rgba(42,42,42,0.06), rgba(42,42,42,0.14), rgba(42,42,42,0.05));
    border-radius: 22px;
  }
  .contact {
    position: absolute; bottom: 58px; left: 60px; right: 60px;
    display: grid; grid-template-columns: 1fr 1px 1fr 1px 1fr; align-items: end;
  }
  .contact__item { text-align: center; font-size: 10.5px; line-height: 1.55; }
  .contact__icon { width: 16px; height: 16px; display: block; margin: 0 auto 6px; }
  .contact__divider { height: 52px; }
  .contact__divider--gold { background: var(--gold); }
  .contact__divider--orange { background: var(--orange); }
  .sheet__footer-bar { position: absolute; left: 0; bottom: 0; width: 100%; height: 14px; background: var(--blue); }
</style>
</head>
<body>
  <article class="sheet">
    <div class="sheet__header-bar"></div>
    <div class="sheet__header-rule"></div>

    <header class="brand">
      <span class="brand__dot"></span>
      <span class="brand__name">Parcelwise HQ</span>
    </header>

    <section class="letter">
      <p class="letter__salutation">Dear Mr. Harlan,</p>
      <p class="letter__para">Lorem Ipsum is simply dummy text of the printing and typesetting industry. Lorem Ipsum has been the industry's standard dummy text ever since the 1500s, when an unknown printer took a galley of type and scrambled it to make a type specimen book. It has survived not only five centuries, but also the leap into electronic typesetting, remaining essentially unchanged.</p>
      <p class="letter__para">The standard chunk of Lorem Ipsum used since the 1500s is reproduced below for those interested. Sections 1.10.32 and 1.10.33 from an early Latin treatise on ethics are also reproduced in their exact original form, accompanied by English versions from a 1914 translation of the work.</p>
      <p class="letter__para">Lorem Ipsum is simply dummy text of the printing and typesetting industry. Lorem Ipsum has been the industry's standard dummy text ever since the 1500s, when an unknown printer took a galley of type and scrambled it to make a type specimen book. It has survived not only five centuries, but also the leap into electronic typesetting, remaining essentially unchanged. It was popularised in the</p>
      <p class="letter__para">The standard chunk of Lorem Ipsum used since the 1500s is reproduced below for those interested. Sections 1.10.32 and 1.10.33 from an early Latin treatise on ethics are also reproduced in their exact original form, accompanied by English versions from a 1914 translation of the work.</p>
      <div class="letter__signature" role="img" aria-label="Handwritten signature of the sender"></div>
    </section>

    <footer class="contact">
      <div class="contact__item contact__item--address">
        <svg class="contact__icon" viewBox="0 0 16 16" aria-hidden="true"><path d="M8 1 C4.7 1 3 3.4 3 6 C3 9.5 8 15 8 15 C8 15 13 9.5 13 6 C13 3.4 11.3 1 8 1 Z" fill="none" stroke="var(--blue)" stroke-width="1.6"/><circle cx="8" cy="6" r="2" fill="var(--blue)"/></svg>
        42 Harbor Lane<br>Fairview, MI 40000
      </div>
      <span class="contact__divider contact__divider--gold"></span>
      <div class="contact__item contact__item--phone">
        <svg class="contact__icon" viewBox="0 0 16 16" aria-hidden="true"><circle cx="8" cy="8" r="7" fill="none" stroke="var(--blue)" stroke-width="1.3"/><path d="M6 4 L7.3 6 L6.5 7 C7 8.3 7.8 9.2 9 9.6 L10 8.7 L12 10 L11 11.8 C8 11.8 4.5 8.5 4.3 5 Z" fill="var(--blue)"/></svg>
        (555) 010-2040<br>(555) 010-7788
      </div>
      <span class="contact__divider contact__divider--orange"></span>
      <div class="contact__item contact__item--web">
        <svg class="contact__icon" viewBox="0 0 16 16" aria-hidden="true" fill="none" stroke="var(--blue)" stroke-width="1.2"><circle cx="8" cy="8" r="7"/><ellipse cx="8" cy="8" rx="3" ry="7"/><path d="M1 8 H15 M2.5 4.5 H13.5 M2.5 11.5 H13.5"/></svg>
        outreach@parcelwisehq.example<br>www.parcelwisehq.example
      </div>
    </footer>

    <div class="sheet__footer-bar"></div>
  </article>
</body>
</html>
```